Trading journal (Ledger Pulse)

I need a design for trading journal application.
I would like to start from dark version of the design and the main goal that it should be pretty intuitive for everyone. I am going to create the app from scratch and I don't have any logo or branding colors, so it is up to you to choose a color scheme but it is a dark mode, so one of the colors would be black obviously.
The app will be available for web PC, Android and iOS.

There is google document with the requirements.
https://files.morvaly.net/page/d/7KpLsW2vQeR9tY4uZ1aBcD3fG5hJ8nM0xZ6oIqEw/view?mode=share

Target Market(s)

Professional traders

Industry/Entity Type

Trading

Colors

Designer to choose colors to be used in the design.

Requirements
Must have
• Dark mode design for PC and mobile views, the design must be pretty intuitive for everyone.
Nice to have
• Tooltips for something non obvious; popovers after completing some actions

```html
<!DOCTYPE html>
<html lang="en">
<head>
<meta charset="utf-8">
<title>Ledger Pulse — Trading Journal</title>
<link href="https://fonts.googleapis.com/css2?family=DM+Sans:wght@400;500;600;700&display=swap" rel="stylesheet">
<style>
:root{
  --page:#ffffff;
  --ink:#0b0b0d;
  --panel:#151518;
  --card:#18181b;
  --line:#3a3a40;
  --text:#f2f2f5;
  --muted:#b9b9c2;
  --violet:#6a3df2;
  --violet-soft:#8c5cf6;
  --lilac:#b56cf2;
  --green:#3ec43e;
  --red:#e0281e;
}
*{box-sizing:border-box;margin:0;padding:0}
html,body{width:1200px;height:725px;overflow:hidden;background:var(--page);font-family:"DM Sans",sans-serif;color:var(--text)}
.canvas{position:relative;width:1200px;height:725px}
.abs{position:absolute}

/* Welcome screen */
.welcome{left:21px;top:21px;width:446px;height:255px;
  background:
    radial-gradient(ellipse 60% 35% at 50% 100%,#5a2cf0 0%,transparent 70%),
    linear-gradient(90deg,#5b2ff0 0%,#8e64d8 35%,#5a3a6a 70%,#2e1f2c 100%);
  box-shadow:0 8px 14px rgba(0,0,0,.35)}
.welcome-card{left:42px;top:30px;width:363px;height:194px;background:var(--ink);border-radius:8px;text-align:center}
.welcome-art{left:163px;top:35px;width:40px;height:37px;border-radius:6px;
  background:radial-gradient(circle at 40% 55%,#8c5cf6,#2a1f3a 75%)}
.welcome-kicker{left:0;right:0;top:89px;font-size:12px;font-weight:400}
.welcome-title{left:0;right:0;top:104px;font-size:25px;font-weight:600;color:var(--violet-soft)}
.welcome-copy{left:50px;right:50px;top:142px;font-size:8px;line-height:13px;color:var(--text)}

/* Profile screen */
.profile{left:21px;top:314px;width:446px;height:255px;background:var(--ink);box-shadow:0 8px 14px rgba(0,0,0,.35);overflow:hidden}
.profile-hero{left:0;top:0;width:225px;height:255px;
  background:radial-gradient(ellipse 70% 45% at 55% 25%,#b27ee0 0%,transparent 70%),
  linear-gradient(180deg,#7048f0 0%,#6a3ef0 45%,#4b25c8 75%,#2a1a50 100%)}
.profile-brand{left:41px;top:114px;font-size:22px;font-weight:600;color:#fff}
.profile-form{left:211px;top:0;width:235px;height:255px;background:var(--ink);border-top-left-radius:14px}
.form-title{left:26px;top:11px;font-size:13px;font-weight:500;color:var(--violet-soft)}
.form-label{left:26px;font-size:6.2px;color:var(--text)}
.form-field{left:26px;width:168px;height:20px;border:1px solid #8d8d94;background:#161619;font-size:6.2px;color:var(--muted);padding-left:7px;display:flex;align-items:center;justify-content:space-between;padding-right:9px}
.form-button{left:26px;top:215px;width:168px;height:18px;background:var(--violet);border-radius:2px;font-size:7px;font-weight:500;display:flex;align-items:center;justify-content:center}

/* Dashboard */
.dash{left:505px;top:21px;width:672px;height:658px;background:linear-gradient(180deg,#19191c,#0e0e10);box-shadow:0 8px 14px rgba(0,0,0,.35);overflow:hidden}
.topbar{left:0;top:0;width:672px;height:37px;background:var(--ink);border-bottom:1px solid #222}
.icon-pill{width:18px;height:18px;border-radius:50%;border:1px solid #444;top:10px;display:flex;align-items:center;justify-content:center;font-size:8px;font-weight:600}
.select{top:10px;width:96px;height:17px;border:1px solid #3b3b40;border-radius:3px;font-size:6.2px;display:flex;align-items:center;gap:5px;padding:0 6px}
.select .chev{margin-left:auto}
.bell{left:635px;background:var(--violet-soft);border:none}

.sidebar{left:0;top:37px;width:94px;height:621px;background:linear-gradient(180deg,#a56cf3 0%,#6a3bf0 35%,#6536ef 70%,#a470f2 100%)}
.nav{position:absolute;left:15px;display:flex;align-items:flex-start;gap:6px;font-size:6.2px;line-height:8px;color:#fff}
.nav svg{flex:none}
.nav-active{left:0;top:52px;width:94px;height:12px;background:rgba(255,255,255,.18)}

.greeting{left:110px;top:55px;font-size:11px;font-weight:500}
.stat{top:87px;width:99px;height:53px;background:var(--card);border:1px solid var(--line);border-radius:3px}
.stat-label{left:9px;top:10px;font-size:6.4px;line-height:7.5px}
.stat-value{left:9px;top:31px;font-size:11px;font-weight:600}
.stat-ring{right:10px;top:12px}

.chart{top:156px;width:265px;height:215px;background:var(--card);border:1px solid var(--line);border-radius:3px}
.chart-title{left:9px;top:10px;font-size:7.5px;font-weight:500}
.chart svg{position:absolute;left:0;top:0}
.axis{font-size:11px;fill:var(--muted);font-family:"DM Sans",sans-serif}

.tab{top:398px;height:18px;border-radius:3px;font-size:7.2px;font-weight:500;display:flex;align-items:center;justify-content:center}
.tab-on{left:110px;width:98px;background:var(--violet)}
.tab-off{left:219px;width:99px;background:#20143f;border:1px solid #3a2a73}

.trades{left:111px;top:430px;width:544px;height:184px;background:var(--card);border:1px solid var(--line);border-radius:3px}
.trades-head{left:0;top:0;width:100%;height:24px;border-bottom:1px solid var(--line)}
.th{top:8px;font-size:7px;font-weight:500}
.td{font-size:5.8px;color:var(--text)}
.ticker-dot{width:11px;height:11px;border-radius:50%;background:var(--violet-soft)}
</style>
</head>
<body>
<main class="canvas">

  <!-- Welcome -->
  <section class="abs welcome">
    <div class="abs welcome-card">
      <div class="abs welcome-art" role="img" aria-label="Celebration party popper illustration"></div>
      <p class="abs welcome-kicker">Welcome to</p>
      <h1 class="abs welcome-title">Ledger Pulse</h1>
      <p class="abs welcome-copy">Ledger Pulse helps you learn from your trade mistakes and become a profitable trader with the power of journaling and analytics.</p>
    </div>
  </section>

  <!-- Complete profile -->
  <section class="abs profile">
    <div class="abs profile-hero" role="img" aria-label="Violet gradient backdrop with faint market chart lines"></div>
    <p class="abs profile-brand">Ledger Pulse</p>
    <div class="abs profile-form">
      <h2 class="abs form-title">Complete Profile</h2>
      <p class="abs form-label" style="top:40px">Enter Display Name</p>
      <div class="abs form-field" style="top:53px"><span>Your Name</span></div>
      <p class="abs form-label" style="top:84px">What is your default account currency?</p>
      <div class="abs form-field" style="top:96px;color:var(--text)"><span>USD</span><span>⌄</span></div>
      <p class="abs form-label" style="top:128px">What is your default time zone?</p>
      <div class="abs form-field" style="top:140px"><span>2024-01-16</span>
        <svg width="7" height="7" viewBox="0 0 10 10"><rect x="1" y="2" width="8" height="7" fill="none" stroke="#ddd"/><path d="M1 4h8M3 1v2M7 1v2" stroke="#ddd"/></svg></div>
      <p class="abs form-label" style="top:171px">What is your trading experience?</p>
      <div class="abs form-field" style="top:183px"><span>Intermediate (1-3 years)</span><span>⌄</span></div>
      <div class="abs form-button">Start Journaling</div>
    </div>
  </section>

  <!-- Dashboard -->
  <section class="abs dash">
    <header class="abs topbar">
      <div class="abs icon-pill" style="left:398px">$</div>
      <div class="abs select" style="left:427px">
        <svg width="7" height="7" viewBox="0 0 10 10"><rect x="1" y="2" width="8" height="7" fill="none" stroke="#ddd"/><path d="M1 4h8" stroke="#ddd"/></svg>
        <span>2024 Jan 16</span><span class="chev">⌄</span></div>
      <div class="abs select" style="left:531px">
        <svg width="7" height="7" viewBox="0 0 10 10"><rect x="1" y="1.5" width="8" height="7" rx="1" fill="none" stroke="#ddd"/><path d="M5 5h4" stroke="#ddd"/></svg>
        <span>All Accounts</span><span class="chev">⌄</span></div>
      <div class="abs icon-pill bell">
        <svg width="8" height="9" viewBox="0 0 10 11"><path d="M2 8V5a3 3 0 0 1 6 0v3l1 1H1z M4 10h2" fill="none" stroke="#fff"/></svg></div>
    </header>

    <nav class="abs sidebar">
      <div class="abs nav-active"></div>
      <div class="nav" style="top:54px"><svg width="9" height="9" viewBox="0 0 10 10" fill="none" stroke="#fff" stroke-width=".9"><rect x=".5" y=".5" width="3.5" height="3.5"/><rect x="6" y=".5" width="3.5" height="3.5"/><rect x=".5" y="6" width="3.5" height="3.5"/><rect x="6" y="6" width="3.5" height="3.5"/></svg>Dashboard</div>
      <div class="nav" style="top:71px"><svg width="9" height="9" viewBox="0 0 10 10" fill="none" stroke="#fff" stroke-width=".9"><path d="M1.5 1v8M4 3v6M6.5 2v7M9 4v5"/></svg>Trade</div>
      <div class="nav" style="top:88px"><svg width="9" height="9" viewBox="0 0 10 10" fill="none" stroke="#fff" stroke-width=".9"><rect x=".5" y="1" width="9" height="8"/><path d="M5 2.5v4M3.5 5l1.5 1.5L6.5 5"/></svg>Import trades</div>
      <div class="nav" style="top:105px"><svg width="9" height="9" viewBox="0 0 10 10" fill="none" stroke="#fff" stroke-width=".9"><rect x=".5" y="1.5" width="9" height="8"/><path d="M.5 4h9M3 .5v2M7 .5v2"/></svg>Calendar</div>
      <div class="nav" style="top:122px"><svg width="9" height="9" viewBox="0 0 10 10" fill="none" stroke="#fff" stroke-width=".9"><path d="M5 1l4.5 2.2L5 5.4.5 3.2z M.5 5.2L5 7.4l4.5-2.2 M.5 7.2L5 9.4l4.5-2.2"/></svg>List view for trades</div>
      <div class="nav" style="top:139px"><svg width="9" height="9" viewBox="0 0 10 10" fill="none" stroke="#fff" stroke-width=".9"><rect x=".5" y="1" width="9" height="8"/><circle cx="3.5" cy="4" r="1.2"/><path d="M2 7.5c.5-1.3 2.5-1.3 3 0M6.5 4h2M7.5 3v2"/></svg>Subscriptions</div>
      <div class="nav" style="top:156px"><svg width="9" height="9" viewBox="0 0 10 10" fill="none" stroke="#fff" stroke-width=".9"><circle cx="5" cy="5" r="1.6"/><circle cx="5" cy="5" r="3.8" stroke-dasharray="1.4 .9"/></svg>Settings</div>
      <div class="nav" style="top:173px"><svg width="9" height="10" viewBox="0 0 10 11" fill="none" stroke="#fff" stroke-width=".9"><rect x="1" y="1" width="8" height="9.5"/><path d="M3 3.5h4M3 5.5h4M3 7.5h4"/></svg>General<br>requirements</div>
      <div class="nav" style="top:552px"><svg width="9" height="9" viewBox="0 0 10 10" fill="none" stroke="#fff" stroke-width=".9"><path d="M6 .5H1v9h5M4 5h5.5M8 3.5 9.5 5 8 6.5"/></svg>Logout</div>
    </nav>

    <h2 class="abs greeting">Good Morning, Ava!</h2>

    <article class="abs stat" style="left:110px">
      <p class="abs stat-label">Total net profit</p>
      <p class="abs stat-value">$97,171</p>
    </article>
    <article class="abs stat" style="left:221px">
      <p class="abs stat-label">Average<br>win/loss</p>
      <p class="abs stat-value">3.45</p>
      <svg class="abs stat-ring" width="28" height="28" viewBox="0 0 28 28"><circle cx="14" cy="14" r="12" fill="none" stroke="var(--red)" stroke-width="2.4"/><path d="M14 26A12 12 0 0 1 14 2" fill="none" stroke="var(--green)" stroke-width="2.4"/></svg>
    </article>
    <article class="abs stat" style="left:332px">
      <p class="abs stat-label">Total number<br>of trades</p>
      <p class="abs stat-value">52</p>
      <svg class="abs stat-ring" width="28" height="28" viewBox="0 0 28 28"><circle cx="14" cy="14" r="12" fill="none" stroke="var(--red)" stroke-width="2.4"/><path d="M14 26A12 12 0 0 1 14 2" fill="none" stroke="var(--green)" stroke-width="2.4"/></svg>
    </article>
    <article class="abs stat" style="left:443px">
      <p class="abs stat-label">Win Rate</p>
      <p class="abs stat-value">50%</p>
      <svg class="abs" style="left:52px;top:17px" width="38" height="28" viewBox="0 0 38 28"><path d="M4 20A15 15 0 0 1 19 5" fill="none" stroke="var(--green)" stroke-width="2.4"/><path d="M19 5A15 15 0 0 1 34 20" fill="none" stroke="var(--red)" stroke-width="2.4"/><text x="2" y="27" font-size="6" fill="#fff" font-family="DM Sans,sans-serif" font-weight="600">50</text><text x="30" y="27" font-size="6" fill="#fff" font-family="DM Sans,sans-serif" font-weight="600">50</text></svg>
    </article>
    <article class="abs stat" style="left:554px">
      <p class="abs stat-label">Fees +<br>Commissions</p>
      <p class="abs stat-value">$97,171</p>
      <svg class="abs stat-ring" width="28" height="28" viewBox="0 0 28 28"><circle cx="14" cy="14" r="12" fill="none" stroke="var(--red)" stroke-width="2.4"/><path d="M14 26A12 12 0 0 1 14 2" fill="none" stroke="var(--green)" stroke-width="2.4"/></svg>
    </article>

    <article class="abs chart" style="left:110px">
      <svg width="265" height="215" viewBox="0 0 541 438">
        <g class="axis" text-anchor="end">
          <text x="42" y="75">$100K</text><text x="42" y="105">$90K</text><text x="42" y="135">$80K</text><text x="42" y="166">$70K</text><text x="42" y="196">$60K</text><text x="42" y="226">$50K</text><text x="42" y="256">$40K</text><text x="42" y="287">$30K</text><text x="42" y="317">$20K</text><text x="42" y="347">$10k</text><text x="42" y="377">$0</text>
        </g>
        <path d="M47 66V374H522" fill="none" stroke="#555" stroke-width="1"/>
        <g class="axis" text-anchor="middle">
          <text x="82" y="414">16/01/2024</text><text x="185" y="414">16/01/2024</text><text x="287" y="414">16/01/2024</text><text x="389" y="414">16/01/2024</text><text x="491" y="414">16/01/2024</text>
        </g>
        <polyline points="65,358 307,351 345,285 380,288 415,233 450,231 485,129" fill="none" stroke="#8a80c8" stroke-width="1.6"/>
      </svg>
      <p class="abs chart-title">Daily Net Cumulative P&amp;L</p>
    </article>

    <article class="abs chart" style="left:389px">
      <svg width="266" height="215" viewBox="0 0 541 438">
        <g class="axis" text-anchor="end">
          <text x="42" y="75">$100K</text><text x="42" y="105">$90K</text><text x="42" y="135">$80K</text><text x="42" y="166">$70K</text><text x="42" y="196">$60K</text><text x="42" y="226">$50K</text><text x="42" y="256">$40K</text><text x="42" y="287">$30K</text><text x="42" y="317">$20K</text><text x="42" y="347">$10k</text><text x="42" y="377">$0</text>
        </g>
        <path d="M47 66V374H522" fill="none" stroke="#555" stroke-width="1"/>
        <g fill="var(--green)">
          <rect x="75" y="366" width="22" height="8"/><rect x="108" y="366" width="22" height="8"/><rect x="141" y="366" width="22" height="8"/><rect x="174" y="366" width="22" height="8"/><rect x="207" y="366" width="22" height="8"/><rect x="240" y="366" width="22" height="8"/>
          <rect x="272" y="194" width="22" height="180"/><rect x="304" y="317" width="22" height="57"/><rect x="372" y="256" width="22" height="118"/><rect x="405" y="219" width="22" height="155"/>
        </g>
        <g fill="var(--red)"><rect x="337" y="374" width="22" height="8"/><rect x="440" y="374" width="22" height="8"/></g>
        <g class="axis" text-anchor="middle">
          <text x="84" y="414">16/01/2024</text><text x="186" y="414">16/01/2024</text><text x="288" y="414">16/01/2024</text><text x="390" y="414">16/01/2024</text><text x="492" y="414">16/01/2024</text>
        </g>
      </svg>
      <p class="abs chart-title">Net Daily P&amp;L</p>
    </article>

    <div class="abs tab tab-on">Recent Trades</div>
    <div class="abs tab tab-off">Open Trades</div>

    <section class="abs trades">
      <div class="abs trades-head"></div>
      <span class="abs th" style="left:28px">Ticker</span>
      <span class="abs th" style="left:125px;top:7px">Entry Price</span>
      <span class="abs th" style="left:211px">Status</span>
      <span class="abs th" style="left:281px">Exit Price</span>
      <span class="abs th" style="left:361px">Current Profit in $</span>
      <span class="abs th" style="left:468px">Current Profit in %</span>

      <div class="abs ticker-dot" style="left:28px;top:38px"></div>
      <span class="abs td" style="left:44px;top:40px">Lorem Ipsum</span><span class="abs td" style="left:125px;top:40px">$150</span><span class="abs td" style="left:211px;top:40px">Open</span><span class="abs td" style="left:281px;top:40px">$150K</span><span class="abs td" style="left:361px;top:40px">$150K</span><span class="abs td" style="left:468px;top:40px">50%</span>

      <div class="abs ticker-dot" style="left:28px;top:67px"></div>
      <span class="abs td" style="left:44px;top:69px">Lorem Ipsum</span><span class="abs td" style="left:125px;top:69px">$150</span><span class="abs td" style="left:211px;top:69px">Open</span><span class="abs td" style="left:281px;top:69px">$150K</span><span class="abs td" style="left:361px;top:69px">$150K</span><span class="abs td" style="left:468px;top:69px">55%</span>

      <div class="abs ticker-dot" style="left:28px;top:96px"></div>
      <span class="abs td" style="left:44px;top:98px">Lorem Ipsum</span><span class="abs td" style="left:125px;top:98px">$150</span><span class="abs td" style="left:211px;top:98px">Closed</span><span class="abs td" style="left:281px;top:98px">$150K</span><span class="abs td" style="left:361px;top:98px">$150K</span><span class="abs td" style="left:468px;top:98px">90%</span>

      <div class="abs ticker-dot" style="left:28px;top:125px"></div>
      <span class="abs td" style="left:44px;top:127px">Lorem Ipsum</span><span class="abs td" style="left:125px;top:127px">$150</span><span class="abs td" style="left:211px;top:127px">Closed</span><span class="abs td" style="left:281px;top:127px">$150K</span><span class="abs td" style="left:361px;top:127px">$150K</span><span class="abs td" style="left:468px;top:127px">50%</span>

      <div class="abs ticker-dot" style="left:28px;top:154px"></div>
      <span class="abs td" style="left:44px;top:156px">Lorem Ipsum</span><span class="abs td" style="left:125px;top:156px">$150</span><span class="abs td" style="left:211px;top:156px">Open</span><span class="abs td" style="left:281px;top:156px">$150K</span><span class="abs td" style="left:361px;top:156px">$150K</span><span class="abs td" style="left:468px;top:156px">50%</span>
    </section>
  </section>

</main>
</body>
</html>
```